WP website design (Harrowgate)

We need a wordpress design for an established auction and real estate company based in Florida. The winning design will incorporate a professional color scheme with company logo in a clean layout. The design needs to consider that this will be developed on a responsive theme. Colors are those that will highlight the logo.

Industry/Entity Type

Real Estate

Font styles to use
Serif
Sans Serif

Colors

Designer to choose colors to be used in the design.

Requirements
Must have
• Navigation:
1) Home
2) Auctions
3) Online Auctions
4) About Us
5) Services
6) Real Estate Listings
7) References
8) Contact Us

Colors will be blue (#000066) / red (#B10000) and black or other complementary color. Tagline to be used "Since 1977, Proven Results." Slideshow to be placed in the header or body of home page - please use stock real estate image.

Widgets: 1) Email Sign-up 2) Social media icons for FB and LinkedIn 3) Featured Listings 4) Testimonials 5) Register button

Footer will have smaller company logo, attached logos and contact info:
Phone: (555) 261-0948 Mobile: (555) 718-3062
Email: mirelharrowgate@quellmail.example
Address: 58 E. Tamsin Avenue, Ste 410, Pensacola, FL 32599
Nice to have
• Use of a drop down menu:
Auctions-
1) Upcoming Auctions
2) Past Auctions

```html
<!DOCTYPE html>
<html lang="en">
<head>
<meta charset="utf-8">
<title>Harrowgate Auctions</title>
<link rel="stylesheet" href="https://fonts.googleapis.com/css2?family=Open+Sans:wght@400;600;700&family=Tinos:wght@400;700&display=swap">
<style>
:root{
  --blue:#1b1f8a;
  --navy:#000066;
  --red:#d71f2b;
  --dark:#222;
  --footer:#262626;
  --grey:#e3e3e3;
  --text:#555;
  --muted:#888;
}
*{box-sizing:border-box;margin:0;padding:0}
html,body{width:766px;height:1200px;overflow:hidden;background:#fff;font-family:"Open Sans",Arial,sans-serif;color:var(--text)}
.page{position:relative;width:766px;height:1200px;border-top:2px solid var(--blue)}
.abs{position:absolute}
.brand{left:65px;top:14px;display:flex;align-items:center;gap:7px}
.brand-mark{width:26px;height:26px;background:var(--blue)}
.brand-name{font-weight:700;font-size:17px;color:var(--blue);letter-spacing:.2px}
.btn{height:18px;width:57px;font-size:7px;font-weight:700;color:#fff;display:flex;align-items:center;justify-content:center;text-transform:uppercase;border-radius:2px}
.btn-login{left:582px;top:16px;background:var(--red)}
.btn-register{left:645px;top:16px;background:#333}
.nav{left:64px;top:52px;width:638px;height:26px;background:var(--blue);display:flex}
.nav a{font-size:8px;color:#fff;text-decoration:none;display:flex;align-items:center;justify-content:center;border-right:1px solid #2f3399;font-weight:600}
.nav a.active{background:var(--red)}
.dropdown{left:119px;top:78px;width:141px;height:48px;background:var(--red)}
.dropdown li{list-style:none;font-size:7.5px;color:#fff;font-weight:600;height:23px;display:flex;align-items:center;padding-left:9px;border-bottom:1px solid #b81520}
.dropdown li::before{content:"";width:3px;height:3px;background:#fff;border-radius:50%;margin-right:6px}
.slider{left:64px;top:88px;width:638px;height:268px;background:linear-gradient(120deg,#f1f1f1,#d6d6d6 45%,#b9b1ab 70%,#e6e4e3);border-bottom:2px solid var(--red)}
.arrow{width:18px;height:18px;border-radius:50%;top:125px}
.caption{left:192px;top:240px;width:264px;height:26px;background:var(--red);border-radius:22px 22px 0 0;color:#fff;font-weight:700;font-size:13px;display:flex;align-items:center;justify-content:center}
.dots{display:flex;gap:4px}
.dots i{width:4px;height:4px;border-radius:50%;background:#ccc}
.dots i.on{background:var(--red)}
.section-title{left:64px;width:638px;text-align:center;font-size:12px;color:#444}
.title-rule{left:64px;width:638px;height:1px;background:#d5d5d5}
.title-rule::after{content:"";position:absolute;left:259px;top:-1px;width:115px;height:2px;background:var(--red)}
.listings{left:64px;top:406px;width:638px;height:289px;background:var(--grey)}
.card{width:194px;height:107px;background:#fff}
.card-img{left:10px;top:10px;width:97px;height:86px}
.card h3{position:absolute;left:112px;top:8px;font-size:10.5px;font-weight:600;color:#555}
.card p{position:absolute;left:112px;top:29px;width:74px;font-size:7px;line-height:9.5px;text-align:justify;color:#777}
.card .date{position:absolute;left:113px;top:76px;width:53px;height:17px;border:1px solid #ccc;font-size:7.5px;display:flex;align-items:center;justify-content:center;color:#555}
.card .eye{position:absolute;left:166px;top:76px;width:17px;height:17px;background:#333;display:flex;align-items:center;justify-content:center}
.card .eye.red{background:var(--red)}
.view-all{left:342px;top:668px;width:88px;height:17px;background:var(--blue);color:#fff;font-size:8.5px;font-weight:600;display:flex;align-items:center;justify-content:center}
.testimonial{width:203px;height:90px}
.avatar{left:0;top:0;width:46px;height:46px;border-radius:50%;border:1px solid #ddd;background:#fff;padding:4px}
.avatar span{display:block;width:100%;height:100%;border-radius:50%;background:#c8b7a8}
.quote{left:65px;top:7px;width:138px;font-family:"Tinos",serif;font-size:8px;line-height:11.5px;text-align:justify;color:#333}
.quote::before{content:"\201C";font-size:34px;color:#ddd;float:left;line-height:26px;margin-right:3px;font-family:Georgia,serif}
.who{left:65px;top:64px;font-family:"Tinos",serif;font-size:8.5px;color:#222}
.role{left:65px;top:79px;font-size:5.5px;color:#999}
.role b{color:#3b6cc9;font-weight:400}
.partner{top:926px;height:50px;background:#e6e6e6}
.footer{left:0;top:990px;width:766px;height:210px;background:var(--footer)}
.fnav{left:0;top:28px;width:766px;display:flex;justify-content:center;font-size:7.5px;color:#bbb;gap:13px}
.fnav span.sep{color:#888}
.frule{left:62px;width:640px;height:1px;background:#3a3a3a}
.fh{font-size:10.5px;color:#ddd}
.social{width:21px;height:20px}
.email-in{left:274px;top:113px;width:128px;height:26px;background:#4a4a4a;font-size:7.5px;color:#999;display:flex;align-items:center;padding-left:11px}
.subscribe{left:402px;top:113px;width:79px;height:26px;background:var(--red);color:#fff;font-weight:700;font-size:10px;display:flex;align-items:center;justify-content:center}
.contact{left:537px;top:92px;width:170px;font-size:7.5px;line-height:12px;color:#777}
.contact div{position:relative;padding-left:22px}
.contact svg{position:absolute;left:0;top:2px}
.copy{left:0;top:1183px;width:766px;text-align:center;font-size:7.5px;color:#666}
</style>
</head>
<body>
<div class="page">
  <div class="abs brand"><span class="brand-mark"></span><span class="brand-name">Harrowgate Auctions</span></div>
  <div class="abs btn btn-login">Login</div>
  <div class="abs btn btn-register">Register</div>

  <nav class="abs nav">
    <a style="width:56px">Home</a>
    <a class="active" style="width:70px">Auctions&nbsp;▾</a>
    <a style="width:96px">Online Auctions</a>
    <a style="width:66px">About Us</a>
    <a style="width:70px">Services</a>
    <a style="width:106px">Real Estate Listings</a>
    <a style="width:80px">References</a>
    <a style="width:94px;border:0">Contact Us</a>
  </nav>

  <div class="abs slider" role="img" aria-label="Stock photo: hand holding a small model house and a set of keys">
    <svg class="abs arrow" style="left:14px" viewBox="0 0 18 18"><circle cx="9" cy="9" r="9" fill="#4a4a8a"/><path d="M10.5 5 6.5 9l4 4" stroke="#fff" stroke-width="1.6" fill="none"/></svg>
    <svg class="abs arrow" style="left:606px" viewBox="0 0 18 18"><circle cx="9" cy="9" r="9" fill="#cfcfcf"/><path d="M7.5 5l4 4-4 4" stroke="#fff" stroke-width="1.6" fill="none"/></svg>
    <div class="abs caption">Since 1977, Proven Results</div>
  </div>
  <ul class="abs dropdown"><li>Upcoming Auctions</li><li>Past Auctions</li></ul>
  <div class="abs dots" style="left:371px;top:364px"><i class="on"></i><i></i><i></i></div>

  <div class="abs section-title" style="top:386px">Featured Listings</div>
  <div class="abs title-rule" style="top:405px"></div>
  <section class="abs listings">
    <div class="abs card" style="left:13px;top:12px"><div class="abs card-img" role="img" aria-label="House with for-sale sign" style="background:linear-gradient(#8fb6dc,#b09068 55%,#4d7a2f)"></div><h3>Lorem contan</h3><p>Lorem ipsum dolor sit amet, consectetur adipiscing</p><div class="date">06/08/2014</div><div class="eye red"><svg width="10" height="7" viewBox="0 0 10 7"><path d="M0 3.5C2 0 8 0 10 3.5 8 7 2 7 0 3.5z" fill="#fff"/><circle cx="5" cy="3.5" r="1.5"/></svg></div></div>
    <div class="abs card" style="left:222px;top:12px"><div class="abs card-img" role="img" aria-label="White two-storey houses" style="background:linear-gradient(#6f95c4,#d8d4c8 55%,#48505a)"></div><h3>Lorem contan</h3><p>Lorem ipsum dolor sit amet, consectetur adipiscing</p><div class="date">06/08/2014</div><div class="eye"><svg width="10" height="7" viewBox="0 0 10 7"><path d="M0 3.5C2 0 8 0 10 3.5 8 7 2 7 0 3.5z" fill="#fff"/><circle cx="5" cy="3.5" r="1.5"/></svg></div></div>
    <div class="abs card" style="left:431px;top:12px"><div class="abs card-img" role="img" aria-label="Villa with pool and lounge chair" style="background:linear-gradient(#2c4a86,#8a7c6a 45%,#3a86a6 60%,#4f8a34)"></div><h3>Lorem contan</h3><p>Lorem ipsum dolor sit amet, consectetur adipiscing</p><div class="date">06/08/2014</div><div class="eye"><svg width="10" height="7" viewBox="0 0 10 7"><path d="M0 3.5C2 0 8 0 10 3.5 8 7 2 7 0 3.5z" fill="#fff"/><circle cx="5" cy="3.5" r="1.5"/></svg></div></div>
    <div class="abs card" style="left:13px;top:134px"><div class="abs card-img" role="img" aria-label="For-sale sign in front of a house" style="background:linear-gradient(#3d6fb8,#c9a98a 50%,#c0272d 65%,#6b8a3a)"></div><h3>Lorem contan</h3><p>Lorem ipsum dolor sit amet, consectetur adipiscing</p><div class="date">06/08/2014</div><div class="eye"><svg width="10" height="7" viewBox="0 0 10 7"><path d="M0 3.5C2 0 8 0 10 3.5 8 7 2 7 0 3.5z" fill="#fff"/><circle cx="5" cy="3.5" r="1.5"/></svg></div></div>
    <div class="abs card" style="left:222px;top:134px"><div class="abs card-img" role="img" aria-label="Suburban home with garden" style="background:linear-gradient(#7fb0e0,#c9b79e 50%,#6a8a3e)"></div><h3>Lorem contan</h3><p>Lorem ipsum dolor sit amet, consectetur adipiscing</p><div class="date">06/08/2014</div><div class="eye"><svg width="10" height="7" viewBox="0 0 10 7"><path d="M0 3.5C2 0 8 0 10 3.5 8 7 2 7 0 3.5z" fill="#fff"/><circle cx="5" cy="3.5" r="1.5"/></svg></div></div>
    <div class="abs card" style="left:431px;top:134px"><div class="abs card-img" role="img" aria-label="Large family house with lawn" style="background:linear-gradient(#2c5aa8,#bfb7ad 50%,#3f7a2c)"></div><h3>Lorem contan</h3><p>Lorem ipsum dolor sit amet, consectetur adipiscing</p><div class="date">06/08/2014</div><div class="eye"><svg width="10" height="7" viewBox="0 0 10 7"><path d="M0 3.5C2 0 8 0 10 3.5 8 7 2 7 0 3.5z" fill="#fff"/><circle cx="5" cy="3.5" r="1.5"/></svg></div></div>
  </section>
  <div class="abs view-all">View All</div>

  <div class="abs section-title" style="top:725px">Testimonials</div>
  <div class="abs title-rule" style="top:747px"></div>

  <div class="abs testimonial" style="left:63px;top:758px">
    <div class="abs avatar" role="img" aria-label="Customer portrait"><span></span></div>
    <p class="abs quote">Pellentesque et pulvinar enim. Quisque at tempor ligula. Donec ut purus sed tortor malesuada.</p>
    <div class="abs who">Corin Ashby</div><div class="abs role">Art Director / <b>lorem ipsum</b></div>
  </div>
  <div class="abs testimonial" style="left:284px;top:758px">
    <div class="abs avatar" role="img" aria-label="Customer portrait"><span></span></div>
    <p class="abs quote">Pellentesque et pulvinar enim. Quisque at tempor ligula. Donec ut purus sed tortor malesuada.</p>
    <div class="abs who">Corin Ashby</div><div class="abs role">Art Director / <b>lorem ipsum</b></div>
  </div>
  <div class="abs testimonial" style="left:502px;top:758px">
    <div class="abs avatar" role="img" aria-label="Customer portrait"><span></span></div>
    <p class="abs quote">Pellentesque et pulvinar enim. Quisque at tempor ligula. Donec ut purus sed tortor malesuada.</p>
    <div class="abs who">Corin Ashby</div><div class="abs role">Art Director / <b>lorem ipsum</b></div>
  </div>
  <div class="abs dots" style="left:369px;top:865px"><i style="background:var(--blue)"></i><i></i><i></i><i></i></div>

  <div class="abs" style="left:64px;top:906px;width:638px;height:1px;background:#ddd"></div>
  <div class="abs partner" style="left:68px;width:55px" aria-label="Partner badge"></div>
  <div class="abs partner" style="left:130px;width:32px" aria-label="Partner badge"></div>
  <div class="abs partner" style="left:172px;width:130px" aria-label="Partner badge"></div>
  <div class="abs partner" style="left:308px;width:70px" aria-label="Partner badge"></div>
  <div class="abs partner" style="left:402px;width:176px" aria-label="Partner badge"></div>
  <div class="abs partner" style="left:598px;width:104px" aria-label="Certificate badge"></div>

  <footer class="abs footer">
    <div class="abs fnav"><span>Home</span><span class="sep">|</span><span>Auctions</span><span class="sep">|</span><span>Online Auctions</span><span class="sep">|</span><span>About Us</span><span class="sep">|</span><span>Services</span><span class="sep">|</span><span>Real Estate Listings</span><span class="sep">|</span><span>References</span><span class="sep">|</span><span>Contact Us</span></div>
    <div class="abs frule" style="top:66px"></div>
    <div class="abs fh" style="left:63px;top:91px">Follow Us</div>
    <div class="abs social" style="left:63px;top:114px;background:#2e4a8f" aria-label="Social profile"></div>
    <div class="abs social" style="left:90px;top:114px;background:#1a78b0" aria-label="Social profile"></div>
    <div class="abs fh" style="left:274px;top:91px;width:207px;text-align:center">News letter</div>
    <div class="abs email-in">Enter your email</div>
    <div class="abs subscribe">Subscribe</div>
    <div class="abs contact">
      <div><svg width="9" height="9" viewBox="0 0 10 10"><path d="M2 0l2 2.5-1 1.5c.8 1.5 1.5 2.2 3 3l1.5-1L10 8 8.5 10C4 9.5.5 6 0 1.5z" fill="#888"/></svg>Phone: (555) 261-0948 Mobile: (555) 718-3062</div>
      <div style="margin-top:3px"><svg width="9" height="7" viewBox="0 0 10 7"><rect width="10" height="7" fill="#888"/><path d="M0 0l5 4 5-4" stroke="#262626" fill="none"/></svg>Email: mirelharrowgate@quellmail.example</div>
      <div><svg width="8" height="10" viewBox="0 0 8 10"><path d="M4 0a4 4 0 0 1 4 4c0 3-4 6-4 6S0 7 0 4a4 4 0 0 1 4-4z" fill="#888"/><circle cx="4" cy="4" r="1.5" fill="#262626"/></svg>Address: 58 E. Tamsin Avenue, Ste 410, Pensacola, FL 32599</div>
    </div>
    <div class="abs frule" style="top:166px"></div>
  </footer>
  <div class="abs copy">Copyright © 2014 yoursite Privacy Policy | Contact Us | Unsubscribe</div>
</div>
</body>
</html>
```